Business card for Luxury Portable Restroom Trailer company

We are a Luxury Portable Restroom Trailer Company Called FALCRIDGE HIRES. Based in Orange County California. We provide portable restroom trailers for events, such as, Weddings, Concerts, Charity events, Sporting events, Tournaments, Corporate events, ect. We rent and Sell the Luxury restrooms. Our colors are white, grey, and Orange. As you will see in the logo we uploaded.
There are 2 people in the company so the names and titles will change for the 3 people but card will remain the same. Here is the information for each Person: Dwight Penner CFO 555 318-0476
next Person: Leon Marchetti VP 555 318-0476
Next Person: Owen Marchetti CEO 555 318-0476
Information to include on the card: Luxury Restroom Trailers Rental and Sales. Weddings, Concerts, Charity, Sporting and Corp. Events.

```html
<!DOCTYPE html>
<html lang="en">
<head>
<meta charset="utf-8">
<title>Falcridge Hires — Business Card</title>
<link rel="stylesheet" href="https://fonts.googleapis.com/css2?family=Arimo:wght@400;700&display=swap">
<style>
  :root {
    --bg: #e6e4e1;
    --card-dark: #4b4b4d;
    --card-light: #f7f7f7;
    --orange: #e8671f;
    --grey-text: #5a5a5c;
    --ink: #2b2b2b;
    --white: #ffffff;
  }
  * { margin: 0; padding: 0; box-sizing: border-box; }
  html, body { width: 1200px; height: 1108px; overflow: hidden; }
  body {
    background: var(--bg);
    font-family: "Arimo", Arial, sans-serif;
    position: relative;
  }
  .card {
    position: absolute;
    left: 150px;
    width: 900px;
    height: 514px;
    border-radius: 30px;
    box-shadow: 0 10px 28px rgba(0,0,0,0.18);
    overflow: hidden;
  }
  /* Back side */
  .card-back { top: 28px; background: var(--card-dark); color: var(--white); }
  .back-logo {
    position: absolute;
    left: 50%; top: 150px;
    transform: translateX(-50%);
    display: flex; align-items: center; gap: 18px;
    border: 4px solid var(--white);
    padding: 22px 40px;
  }
  .back-logo .wordmark {
    font-weight: 700; font-size: 58px; letter-spacing: 2px;
    color: var(--white); white-space: nowrap;
  }
  .logo-dot { width: 26px; height: 26px; border-radius: 50%; background: var(--orange); flex: none; }
  .tagline {
    position: absolute; left: 0; right: 0; top: 330px;
    text-align: center; font-size: 21px; line-height: 1.45;
  }
  /* Front side */
  .card-front { top: 566px; background: var(--card-light); color: var(--ink); }
  .front-logo {
    position: absolute; left: 56px; top: 48px;
    display: flex; align-items: center; gap: 12px;
    border: 3px solid var(--grey-text);
    padding: 12px 22px;
  }
  .front-logo .wordmark {
    font-weight: 700; font-size: 30px; letter-spacing: 1px; color: var(--grey-text);
  }
  .front-logo .logo-dot { width: 16px; height: 16px; }
  .person { position: absolute; left: 56px; top: 148px; }
  .person-name { font-weight: 700; font-size: 34px; color: var(--orange); letter-spacing: 1px; }
  .person-title { font-size: 20px; color: var(--grey-text); margin-top: 4px; }
  .address { position: absolute; left: 56px; top: 236px; font-size: 21px; line-height: 1.4; }
  .contacts { position: absolute; left: 56px; top: 318px; list-style: none; font-size: 21px; line-height: 1.55; }
  .contacts li { display: flex; align-items: center; gap: 12px; }
  .contacts svg { width: 16px; height: 16px; flex: none; }
  .emblem { position: absolute; right: 90px; top: 77px; width: 360px; height: 360px; }
</style>
</head>
<body>

<section class="card card-back" aria-label="Card back">
  <div class="back-logo">
    <span class="logo-dot"></span>
    <span class="wordmark">FALCRIDGE HIRES</span>
  </div>
  <p class="tagline">
    Luxury Restroom Trailers Rental and Sales<br>
    Weddings, Concerts, Charity, Sporting and Corp Events
  </p>
</section>

<section class="card card-front" aria-label="Card front">
  <div class="front-logo">
    <span class="logo-dot"></span>
    <span class="wordmark">FALCRIDGE HIRES</span>
  </div>
  <div class="person">
    <h1 class="person-name">DWIGHT PENNER</h1>
    <p class="person-title">CFO</p>
  </div>
  <p class="address">2170 Harlow Crest Drive<br>Brookvale, NY 11520</p>
  <ul class="contacts">
    <li>
      <svg viewBox="0 0 16 16" aria-hidden="true"><path fill="#e8671f" d="M3.6 1.5l2.3 2.6-1.3 1.6c.9 2 2.6 3.7 4.6 4.6l1.6-1.3 2.6 2.3-1.2 2.2C7 13.3 2.7 9 1.4 2.7z"/></svg>
      555 318-0476
    </li>
    <li>
      <svg viewBox="0 0 16 16" aria-hidden="true"><rect x="1" y="3.5" width="14" height="9" rx="1" fill="#e8671f"/><path d="M1.5 4l6.5 5 6.5-5" stroke="#fff" stroke-width="1.3" fill="none"/></svg>
      name@falcridgehires.com
    </li>
    <li>
      <svg viewBox="0 0 16 16" aria-hidden="true"><circle cx="8" cy="8" r="7" fill="#e8671f"/><path d="M1 8h14M8 1c-3 3.5-3 10.5 0 14M8 1c3 3.5 3 10.5 0 14" stroke="#fff" stroke-width="1" fill="none"/></svg>
      www.falcridgehires.com
    </li>
  </ul>
  <svg class="emblem" viewBox="0 0 360 360" aria-hidden="true">
    <circle cx="180" cy="180" r="168" fill="none" stroke="var(--orange)" stroke-width="16"/>
  </svg>
</section>

</body>
</html>
```